Luxury Wine Label for New Startup Winery

We need a wine label for our new winery startup. We have worked with a local designer but do not feel the resulting label / logo have the elevation required to present our brand as a luxury wine. Our winery is called "Quailbrook Vineyards" and we are focused on extremely high quality hand crafted artisan and estate wines from the Pacific Northwest.
We would like to see designs that utilize a tree line, or other imagery that represents the "Quailbrook" part of our company name. Another interesting feature could be wood grain.
A logo will be required based on your design so please design with this in mind:
This logo should be consistent with the wine bottle label design, and should be representative of our high end exclusive wine while giving a sense of place (Oregon/ Pacific Northwest.)
I will supply an image of the design we received from our local designer, PLEASE NOTE: in general we do like wood grain and tree line concepts but feel the execution was poorly done.
ATTN: Logo design should be suitable for use on: Bottles (Red wine/rose/white wine), Bussiness cards, vehicle signage, business signage, etc
P.S.:
If you have a design that is not outside the box we are still interested in seeing it.
Label is for a burgundy style bottle with a label height of 3.5 - 4" and a width of 3.5-4"
any label <= 4"x4" and >=3.5"x3.5" will be acceptable:
HOWEVER Width should be greater than or equal to height due to the bottle format
Target Market(s)
Wine enthusiasts with adequate discretionary budgets to afford $100 bottles of wine.
Industry/Entity Type
Wine / Winery
Requirements
Must have
- A sense of luxury, a feel of exclusivity, and a theme consistent with our product and brand name
Nice to have
- Tree line, wood grain or other wood themes. Serif fonts
Should not have
- anything cheesy, off topic, hard to read script fonts or anything that makes the label hard to read from a few feet away or too busy

```html
<!DOCTYPE html>
<html lang="en">
<head>
<meta charset="utf-8">
<title>Quailbrook Vineyards — Syrah Label</title>
<link href="https://fonts.googleapis.com/css2?family=Cinzel:wght@400;500;600&family=Pinyon+Script&display=swap" rel="stylesheet">
<style>
  :root {
    --bg: #ecf0f1;
    --label-black: #000000;
    --rule-olive: #6f6a4f;
    --gold-deep: #cdb752;
    --gold-pale: #f1ebd8;
    --gold-mid: #d9c87c;
    --wood-dark: #311a14;
    --wood-mid: #733a22;
    --wood-warm: #7a3d24;
    --tan: #d5a876;
    --tan-muted: #b98a5e;
  }
  html, body {
    margin: 0;
    width: 1200px;
    height: 1200px;
    overflow: hidden;
    background: var(--bg);
  }
  .canvas {
    position: relative;
    width: 1200px;
    height: 1200px;
  }
  .main-label {
    position: absolute;
    left: 299px; top: 319px;
    width: 602px; height: 401px;
    background: var(--label-black);
  }
  .rule {
    position: absolute;
    left: 17px; width: 566px; height: 5px;
    background: var(--rule-olive);
  }
  .rule.top { top: 33px; }
  .rule.bottom { top: 369px; }
  .treeline {
    position: absolute;
    left: 17px; top: 38px;
    width: 566px; height: 162px;
  }
  .brand {
    position: absolute;
    left: 0; width: 100%;
    text-align: center;
    font-family: "Cinzel", serif;
    text-transform: uppercase;
    background: linear-gradient(90deg, var(--gold-deep) 22%, var(--gold-pale) 52%, var(--gold-mid) 82%);
    -webkit-background-clip: text;
    background-clip: text;
    color: transparent;
    margin: 0;
    line-height: 1;
    white-space: nowrap;
  }
  .brand-name {
    top: 196px;
    font-size: 48px;
    font-weight: 600;
    letter-spacing: 0.16em;
    padding-left: 0.16em;
  }
  .brand-sub {
    top: 250px;
    font-size: 48px;
    font-weight: 600;
    letter-spacing: 0.16em;
    padding-left: 0.16em;
  }
  .region {
    top: 314px;
    font-size: 31px;
    font-weight: 600;
    letter-spacing: 0.1em;
    padding-left: 0.1em;
  }
  .varietal-label {
    position: absolute;
    left: 300px; top: 739px;
    width: 599px; height: 141px;
    overflow: hidden;
  }
  .wood {
    position: absolute; inset: 0;
    background:
      linear-gradient(180deg, rgba(49,26,20,0.55) 0%, rgba(49,26,20,0) 10%, rgba(49,26,20,0) 40%, rgba(49,26,20,0.35) 50%, rgba(49,26,20,0) 60%, rgba(49,26,20,0) 85%, rgba(49,26,20,0.5) 100%),
      linear-gradient(90deg, var(--wood-mid), var(--wood-warm) 50%, var(--wood-mid));
  }
  .tan-rule {
    position: absolute;
    height: 5px;
    background: var(--tan);
  }
  .tan-rule.top { left: 17px; top: 12px; width: 566px; }
  .tan-rule.left { left: 17px; top: 123px; width: 107px; }
  .tan-rule.right { left: 476px; top: 123px; width: 107px; }
  .varietal {
    position: absolute;
    left: 0; width: 100%; top: 6px;
    margin: 0;
    text-align: center;
    font-family: "Pinyon Script", cursive;
    font-weight: 400;
    font-size: 88px;
    line-height: 1;
    color: var(--tan);
  }
  .vintage-line {
    position: absolute;
    left: 0; width: 100%; top: 114px;
    margin: 0;
    text-align: center;
    font-family: "Cinzel", serif;
    text-transform: uppercase;
    font-size: 19px;
    letter-spacing: 0.08em;
    color: var(--tan-muted);
    line-height: 1;
    white-space: nowrap;
  }
  .vintage-line .divider { padding: 0 8px; }
</style>
</head>
<body>
<main class="canvas">
  <section class="main-label">
    <div class="rule top"></div>
    <svg class="treeline" viewBox="0 0 566 162" role="img" aria-label="Gold tree line silhouette along a sweeping hillside">
      <defs>
        <linearGradient id="goldSweep" x1="0" y1="0" x2="1" y2="0">
          <stop offset="0" stop-color="#cdb752"/>
          <stop offset="0.55" stop-color="#f1ebd8"/>
          <stop offset="1" stop-color="#d9c87c"/>
        </linearGradient>
      </defs>
      <path d="M0 0 C60 10 110 10 170 22 C230 34 270 42 320 46 C380 54 420 66 470 74 C510 82 540 76 566 88 L566 162 C470 130 330 128 210 118 C110 110 45 100 0 80 Z" fill="url(#goldSweep)"/>
    </svg>
    <h1 class="brand brand-name">Quailbrook</h1>
    <p class="brand brand-sub">Vineyards</p>
    <p class="brand region">Wiliamette Valley</p>
    <div class="rule bottom"></div>
  </section>

  <section class="varietal-label">
    <div class="wood" role="img" aria-label="Dark walnut wood grain texture"></div>
    <div class="tan-rule top"></div>
    <h2 class="varietal">Syrah</h2>
    <div class="tan-rule left"></div>
    <p class="vintage-line">Estate<span class="divider">|</span>2023<span class="divider">|</span>Grown</p>
    <div class="tan-rule right"></div>
  </section>
</main>
</body>
</html>
```